BUSINESS CARD - HALLORAN FIELD SERVICES

I would like to create a business card for my fertilizer spreading business. I would like to incorporate my existing logo and also a description of the services offered. The business card will be given to farmers so must be kept simple but effective. It will also be left in stores so much also be eye catching in order to stand out from other cards.

Target Market(s)

FARMERS

Requirements
Must have
• FRONT OF CARD = EXISTING LOGO + "CUSTOMISED SPREADING" below the logo

REAR Of CARD = SERVICES OFFERED AND CONTACT DETAILS

- Bulk fertilizer including Lime, Gypsum, Manure & Compost
- Granular fertilizer including Single Super, Urea, Gran-am, & Custom Blends
- Modern equipment - Autosteer & Variable Rate Capable
- Friendly & Reliable Service
- Contact Gus: 0417 552 308
Nice to have
• utilize same color scheme as existing logo

```html
<!DOCTYPE html>
<html lang="en">
<head>
<meta charset="utf-8">
<title>Halloran Field Services – Business Card</title>
<link rel="stylesheet" href="https://fonts.googleapis.com/css2?family=Arimo:wght@400;700&display=swap">
<style>
  :root {
    --page-bg: #111111;
    --card-bg: #1d1d1d;
    --accent: #f7941d;
    --logo-grey: #6b6b6b;
    --text-light: #f2f2f2;
    --rule: #4a4a4a;
  }
  * { box-sizing: border-box; margin: 0; padding: 0; }
  html, body {
    width: 1200px;
    height: 900px;
    overflow: hidden;
    background: var(--page-bg);
    font-family: "Arimo", Arial, sans-serif;
  }
  .card-sheet {
    width: 1200px;
    height: 900px;
    display: flex;
    flex-direction: column;
    align-items: center;
    justify-content: center;
    gap: 40px;
  }
  .business-card {
    position: relative;
    width: 700px;
    height: 400px;
    background: var(--card-bg);
    display: flex;
    flex-direction: column;
    align-items: center;
    justify-content: center;
    box-shadow: 0 12px 30px rgba(0,0,0,0.6);
    overflow: hidden;
  }
  .accent-band {
    position: absolute;
    left: 0;
    right: 0;
    bottom: 0;
    height: 12px;
    background: var(--accent);
  }

  /* Front */
  .brand-lockup {
    display: flex;
    align-items: center;
    gap: 18px;
    margin-bottom: 34px;
  }
  .brand-mark {
    width: 64px;
    height: 64px;
    border-radius: 50%;
    background: var(--logo-grey);
  }
  .brand-name {
    color: var(--logo-grey);
    font-weight: 700;
    font-size: 38px;
    letter-spacing: 1px;
    line-height: 1.1;
  }
  .tagline {
    color: var(--accent);
    font-size: 26px;
    letter-spacing: 4px;
    text-transform: uppercase;
  }

  /* Back */
  .services-list {
    list-style: none;
    text-align: center;
    color: var(--text-light);
    font-size: 19px;
    line-height: 1.45;
  }
  .divider {
    width: 260px;
    height: 1px;
    background: var(--rule);
    margin: 20px 0 16px;
  }
  .contact-line {
    color: var(--accent);
    font-size: 32px;
  }
</style>
</head>
<body>
  <main class="card-sheet">
    <section class="business-card card-front" aria-label="Card front">
      <div class="brand-lockup">
        <span class="brand-mark" aria-hidden="true"></span>
        <span class="brand-name">HALLORAN FIELD SERVICES</span>
      </div>
      <p class="tagline">Customised Spreading</p>
      <div class="accent-band"></div>
    </section>

    <section class="business-card card-back" aria-label="Card back">
      <ul class="services-list">
        <li>Bulk fertilizer including Lime, Gypsum, Manure &amp; Compost</li>
        <li>Granular fertilizer including Single Super, Urea</li>
        <li>Gran-am, &amp; Custom Blends</li>
        <li>Modern equipment</li>
        <li>Autosteer &amp; Variable Rate Capable</li>
        <li>Friendly &amp; Reliable Service</li>
      </ul>
      <div class="divider"></div>
      <p class="contact-line">Contact Gus: 0417 552 308</p>
      <div class="accent-band"></div>
    </section>
  </main>
</body>
</html>
```